Road Construction Company needs business cards

We would like a new business card designed for our business.

We're a road construction company based in Qld, Australia.

Can the business card please have the following information on it.

Name: Warren Halbeck
Position: General Manager
Phone: 0472 915 348
Email: Warren.halbeck@tovrin.com.au
Address: 87 Marrow Ave, Pendlebay, QLD, 4023
Website: www.tovrin.com.au

Visually we'd like the card to be professional and simple.

Attached is our logo.

Our website is www.tovrin.com.au

Target Market(s)

Men aged 25-60

Contact Information for Business Card

As listed in project description

Font styles to use
Serif

Requirements
Must have
• Large logo on back of card

```html
<!DOCTYPE html>
<html lang="en">
<head>
<meta charset="utf-8">
<title>Tovrin Road Construction – Business Cards</title>
<link rel="stylesheet" href="https://fonts.googleapis.com/css2?family=Open+Sans:wght@400;600;700;800&display=swap">
<style>
  :root {
    --stage: #2b2e33;
    --card-dark: #222226;
    --card-blue: #1157a9;
    --brand-blue: #1e63b8;
    --accent-blue: #3a9fdc;
    --text-light: #f2f3f5;
    --rule: #8a8d93;
  }
  * { box-sizing: border-box; margin: 0; padding: 0; }
  html, body {
    width: 1200px; height: 780px; overflow: hidden;
    background: var(--stage);
    font-family: "Open Sans", Arial, sans-serif;
  }
  .stage {
    width: 1200px; height: 780px;
    display: flex; align-items: center; justify-content: center; gap: 40px;
  }
  .card {
    width: 540px; height: 309px;
    position: relative; overflow: hidden;
  }
  /* Front: contact side */
  .card--front { background: var(--card-dark); }
  .front__brand {
    position: absolute; left: 38px; top: 52px; width: 220px;
  }
  .brand-name {
    font-weight: 800; font-size: 50px; letter-spacing: 1px; line-height: 1;
    color: var(--brand-blue);
  }
  .front__divider {
    position: absolute; left: 272px; top: 44px; width: 1px; height: 220px;
    background: var(--rule);
  }
  .front__details {
    position: absolute; left: 292px; top: 44px; right: 16px;
    color: var(--text-light);
  }
  .person-name {
    font-weight: 700; font-size: 27px; line-height: 1.1; color: var(--accent-blue);
  }
  .person-role { font-size: 14px; margin-top: 4px; }
  .address { font-size: 13px; line-height: 1.45; margin-top: 14px; }
  .contact-list { list-style: none; margin-top: 12px; font-size: 13px; line-height: 1.55; }
  .contact-list li { display: flex; align-items: center; gap: 8px; white-space: nowrap; }
  .contact-icon { width: 12px; height: 12px; flex: none; }
  /* Back: large brand side */
  .card--back {
    background: var(--card-blue);
    display: flex; align-items: center; justify-content: center;
  }
  .card--back .brand-name {
    color: #ffffff; font-size: 104px; letter-spacing: 3px;
  }
</style>
</head>
<body>
<main class="stage">
  <section class="card card--front" aria-label="Business card front">
    <div class="front__brand"><div class="brand-name">TOVRIN</div></div>
    <div class="front__divider"></div>
    <div class="front__details">
      <h1 class="person-name">Warren Halbeck</h1>
      <p class="person-role">General Manager</p>
      <p class="address">87 Marrow Ave,<br>Pendlebay, QLD, 4023</p>
      <ul class="contact-list">
        <li>
          <svg class="contact-icon" viewBox="0 0 12 12" aria-hidden="true"><path d="M3 1 L5 3.5 L4 4.8 Q5 7 7.2 8 L8.5 7 L11 9 L9.6 11 Q4.5 10.5 1 3 Z" fill="#3a9fdc"/></svg>
          0472 915 348
        </li>
        <li>
          <svg class="contact-icon" viewBox="0 0 12 12" aria-hidden="true"><circle cx="6" cy="6" r="5.2" fill="none" stroke="#3a9fdc" stroke-width="1.2"/><path d="M0.8 6 H11.2 M6 0.8 Q3 6 6 11.2 M6 0.8 Q9 6 6 11.2" fill="none" stroke="#3a9fdc" stroke-width="0.9"/></svg>
          www.tovrin.com.au
        </li>
        <li>
          <svg class="contact-icon" viewBox="0 0 12 12" aria-hidden="true"><rect x="0.8" y="2.2" width="10.4" height="7.6" rx="1" fill="none" stroke="#3a9fdc" stroke-width="1.2"/><path d="M1 2.6 L6 6.6 L11 2.6" fill="none" stroke="#3a9fdc" stroke-width="1.1"/></svg>
          Warren.halbeck@tovrin.com.au
        </li>
      </ul>
    </div>
  </section>

  <section class="card card--back" aria-label="Business card back">
    <div class="brand-name">TOVRIN</div>
  </section>
</main>
</body>
</html>
```